Business Card Design

We are a manufacturing and distribution company with most of our customer base being supermarkets. We have established brand guidelines that are attached.

```html
<!DOCTYPE html>
<html lang="en">
<head>
<meta charset="utf-8">
<title>Corvane Business Card</title>
<link rel="stylesheet" href="https://fonts.googleapis.com/css2?family=Montserrat:wght@400;500;700;800&display=swap">
<style>
  :root {
    --backdrop: #6e6e6e;
    --card: #ffffff;
    --ink: #0d0d0d;
    --brand-red: #e5141e;
    --brand-blue: #1565c0;
    --muted: #555555;
    --ghost: #ececee;
  }
  * { box-sizing: border-box; margin: 0; padding: 0; }
  html, body {
    width: 1200px;
    height: 1056px;
    overflow: hidden;
    background: var(--backdrop);
    font-family: "Montserrat", Arial, sans-serif;
  }
  .sheet {
    position: relative;
    width: 1200px;
    height: 1056px;
  }
  .card {
    position: absolute;
    left: 300px;
    width: 600px;
    height: 343px;
    background: var(--card);
    box-shadow: 0 14px 30px rgba(0,0,0,0.28);
    overflow: hidden;
  }
  .card--front { top: 150px; }
  .card--back { top: 563px; }

  /* Front */
  .wordmark {
    position: absolute;
    left: 0;
    right: 0;
    top: 118px;
    display: flex;
    justify-content: center;
    align-items: center;
    gap: 16px;
  }
  .wordmark__square {
    width: 30px;
    height: 30px;
    background: var(--brand-red);
  }
  .wordmark__name {
    font-weight: 800;
    font-size: 50px;
    letter-spacing: 3px;
    color: var(--ink);
  }
  .rule {
    position: absolute;
    top: 262px;
    height: 5px;
  }
  .rule--red { left: 72px; width: 228px; background: var(--brand-red); }
  .rule--blue { left: 300px; width: 228px; background: var(--brand-blue); }

  /* Back */
  .ghost-name {
    position: absolute;
    right: 38px;
    top: 176px;
    font-weight: 800;
    font-size: 40px;
    letter-spacing: 3px;
    color: var(--ghost);
  }
  .person {
    position: absolute;
    left: 56px;
    top: 62px;
  }
  .person__name {
    font-size: 32px;
    line-height: 1.05;
    letter-spacing: 0.5px;
  }
  .person__first { color: var(--brand-red); font-weight: 800; }
  .person__last { color: var(--brand-blue); font-weight: 500; }
  .person__role {
    font-size: 18px;
    color: var(--muted);
    font-weight: 500;
    margin-top: 2px;
  }
  .contacts {
    position: absolute;
    left: 56px;
    bottom: 40px;
    list-style: none;
  }
  .contacts__item {
    display: flex;
    align-items: center;
    gap: 8px;
    font-size: 13px;
    color: #333;
    margin-top: 8px;
  }
  .contacts__icon {
    width: 18px;
    height: 18px;
    background: var(--brand-blue);
    border-radius: 3px;
    display: flex;
    align-items: center;
    justify-content: center;
  }
</style>
</head>
<body>
<main class="sheet">
  <section class="card card--front" aria-label="Card front">
    <div class="wordmark">
      <span class="wordmark__square"></span>
      <span class="wordmark__name">CORVANE</span>
    </div>
    <div class="rule rule--red"></div>
    <div class="rule rule--blue"></div>
  </section>

  <section class="card card--back" aria-label="Card back">
    <div class="ghost-name" aria-hidden="true">CORVANE</div>
    <div class="person">
      <p class="person__name"><span class="person__first">MARA</span> <span class="person__last">ELLIS</span></p>
      <p class="person__role">Manager</p>
    </div>
    <ul class="contacts">
      <li class="contacts__item">
        <span class="contacts__icon">
          <svg width="12" height="12" viewBox="0 0 24 24"><path fill="#fff" d="M6.6 10.8a15.1 15.1 0 0 0 6.6 6.6l2.2-2.2c.3-.3.7-.4 1-.2 1.1.4 2.3.6 3.6.6.6 0 1 .4 1 1V20c0 .6-.4 1-1 1A17 17 0 0 1 3 4c0-.6.4-1 1-1h3.5c.6 0 1 .4 1 1 0 1.3.2 2.5.6 3.6.1.3 0 .7-.2 1z"/></svg>
        </span>
        (555) 014-2387
      </li>
      <li class="contacts__item">
        <span class="contacts__icon">
          <svg width="12" height="12" viewBox="0 0 24 24"><rect x="2" y="5" width="20" height="14" rx="1" fill="none" stroke="#fff" stroke-width="2"/><path d="M2 6l10 7 10-7" fill="none" stroke="#fff" stroke-width="2"/></svg>
        </span>
        info@corvanemail.com
      </li>
      <li class="contacts__item">
        <span class="contacts__icon">
          <svg width="12" height="12" viewBox="0 0 24 24"><path fill="#fff" d="M5 3l14 7-6 2-2 6z"/></svg>
        </span>
        www.corvane.com
      </li>
    </ul>
  </section>
</main>
</body>
</html>
```